A website where experts collaborate on your project

I am building a new website where experts (yes, like designers) collaborate on projects with the project owner. More minds = more collaboration = better end product. Please see Pelmora(dot)com for a quick landing page I created for collaborating on presentations (although there will be many project types offered)

I am looking for a DESIGNER LONG TERM, but for now, just need initial mock ups to show the web programmers.

I have 21 Word documents loosely designed, what I would like to see here is a theme. Please DO NOT GO OFF WHAT YOU CURRENTLY SEE AT PELMORA. What is up now is only a quick landing page.

You can view a Word doc of the homepage here:
https://www.filevanta.com/s/qx83kdm2/home.docx?dl=0

WHAT AM I LOOKING FOR?
A clean, well designed theme.

Here is a link to the logo:
https://www.filevanta.com/s/mr47tpz9/logo%20-%20horizontal.tif?dl=0
-----------------------------------------
Here are a few sites I like the design of and what I like about them:
www.quenbrook.com-all around my favorite, beautiful graphics, clean layout, bold use of colors on a dark background
Ravelto.com- clean layout, The use of humans and bubble style elements.
Mintharbor.com :) clean, bold, unique pop art style but professional
plumevault.com - From the unique colors and artwork and the ability of that art to not interfere with the important elements of the site
sparkwidgets.com-clean, nice colors, well organized and separated sections.
www.dunmereco.com-love the font, use of colors and sectionalized style

All in all, I am not picky and open to so many styles. I would ultimately like the designer I pick to design all 21 pages.
Updates

Hello everyone,Moving forward, I would like you all to pay special attention to the section in my brief titled "Here are a few sites I like the design of and what I like about them". Please see below, I handpicked each one of these as sites I really like. Thank you.Here are a few sites I like the design of and what I like about them:Ravelto.com- clean layout, The use of humans and bubble style elements.Mintharbor.com :) clean, bold, unique pop art style but professionalwriteraccess.com - From the unique colors and artwork and the ability of that art to not interfere with the important elements of the sitegrowthgeeks.com-clean, nice colors, well organized and separated sections.www.dunmereco.com-love the font, use of colors and sectionalized stylewww.quenbrook.com-beautiful graphics, clean layout, bold use of colors----------------------------------------- Added Tuesday, November 24, 2015

I updated the homepage, you can see it here:https://www.dropbox.com/s/kwlkbsookq3cg2m/1new%20homepage.docx?dl=0I am modeling it after my favorite designed site: triplelift.comI love the dark colors with the orange glowing style boldness of the buttons. It's real clean too. Added Tuesday, November 24, 2015

Target Market(s)

small business owners, marketers, freelancer writers, graphic designers,

Industry/Entity Type

Building

Number of Pages Required

5+ page

Requirements
Must have
• I can't think of anything the project must have.
Nice to have
• WHAT AM I LOOKING FOR?
• A clean, well designed theme. I had a designer do a bit of work putting elements together, I found it to be very plain, but I like the Application Page (https://www.filevanta.com/s/jb19ckr3/Pelmora-Website.ai?dl=0)
• Here is a link to the logo:
• https://www.filevanta.com/s/mr47tpz9/logo%20-%20horizontal.tif?dl=0
• Here are a few sites I like the design of and what I like about them:
• Ravelto.com- clean layout, The use of humans and bubble style elements.
• Mintharbor.com :) clean, bold, unique pop art style but professional
• plumevault.com - From the unique colors and artwork and the ability of that art to not interfere with the important elements of the site
• sparkwidgets.com-clean, nice colors, well organized and separated sections.
• www.dunmereco.com-love the font, use of colors and sectionalized style
• www.quenbrook.com-beautiful graphics, clean layout, bold use of colors
• -----------------------------------------
Should not have
• out of the boxed, templated style website. I want this site to be memorable and not look like a thousand others

```html
<!DOCTYPE html>
<html lang="en">
<head>
<meta charset="utf-8">
<title>Pelmora — Expert Collaboration</title>
<link href="https://fonts.googleapis.com/css2?family=PT+Sans:wght@400;700&display=swap" rel="stylesheet">
<style>
:root{
  --blue:#4aaec9;
  --blue-dark:#3a9fbc;
  --orange:#f7941d;
  --orange-deep:#ee6a12;
  --ink:#444;
  --muted:#8a8a8a;
  --line:#e6e6e6;
  --panel:#f7f7f7;
  --white:#fff;
}
*{box-sizing:border-box;margin:0;padding:0}
html,body{width:1200px;height:2192px;overflow:hidden;background:var(--white)}
body{font-family:"PT Sans",Arial,sans-serif;color:var(--ink);position:relative}

/* header */
.site-header{position:absolute;left:0;top:0;width:1200px;height:102px;background:var(--white)}
.brand{position:absolute;left:129px;top:38px;font-size:25px;font-weight:700;color:var(--blue);line-height:1}
.main-nav{position:absolute;right:129px;top:46px;display:flex;gap:24px}
.main-nav a{font-size:14px;color:var(--blue);text-decoration:none;text-transform:uppercase;position:relative;padding-bottom:16px}
.main-nav a.active{color:var(--orange)}
.main-nav a.active::after{content:"";position:absolute;left:-3px;right:-3px;bottom:0;height:2px;background:var(--orange)}

/* hero */
.hero{position:absolute;left:0;top:102px;width:1200px;height:497px}
.hero-photo{position:absolute;left:425px;top:0;width:775px;height:497px;
  background:linear-gradient(90deg,#2b2f33 0%,#1e2226 40%,#3a4247 62%,#7f9aa3 82%,#a8bfc6 100%)}
.hero-panel{position:absolute;left:0;top:0;width:425px;height:497px;background:var(--blue)}
.hero-title{position:absolute;left:131px;top:203px;font-size:25px;color:var(--white);font-weight:400}
.hero-sub{position:absolute;left:131px;top:242px;font-size:16px;line-height:25px;color:#e9f6fa;width:270px}
.btn-start{position:absolute;left:129px;top:328px;width:137px;height:41px;background:var(--orange);color:var(--white);
  font-size:16px;text-transform:uppercase;display:flex;align-items:center;justify-content:center}
.hero-dots{position:absolute;left:129px;top:431px;display:flex;gap:7px}
.hero-dots span{width:9px;height:9px;border-radius:50%;background:var(--white)}
.hero-dots span.on{background:var(--orange)}
.hero-aside{position:absolute;left:855px;top:200px;color:var(--white)}
.hero-aside h2{font-size:24px;font-weight:400;line-height:33px}
.hero-aside ul{list-style:none;margin-top:12px}
.hero-aside li{font-size:15px;line-height:25px;padding-left:34px;position:relative}
.hero-aside li::before{content:"";position:absolute;left:4px;top:8px;border-left:6px solid var(--orange);border-top:4px solid transparent;border-bottom:4px solid transparent}

/* filters */
.filters{position:absolute;left:117px;top:640px;width:234px}
.filters-head{height:40px;background:linear-gradient(90deg,var(--orange-deep),var(--orange) 60%,#fbb040);
  color:var(--white);font-weight:700;font-size:14px;text-transform:uppercase;display:flex;align-items:center;padding-left:23px;width:234px}
.filters-body{padding-left:12px;width:218px}
.f-label{font-size:11px;color:#555;margin-top:15px}
.f-field{height:24px;border:1px solid #eee;font-size:8px;color:#bbb;padding:7px 5px 0;margin-top:6px}
.price-range{display:flex;justify-content:space-between;font-size:8px;color:#aaa;margin-top:5px}
.slider{position:relative;height:10px;margin-top:2px}
.slider::before{content:"";position:absolute;left:0;right:0;top:4px;height:2px;background:#e5e5e5}
.slider span{position:absolute;left:14px;top:0;width:11px;height:11px;border-radius:50%;background:var(--orange)}
.btn-save{margin-top:14px;width:114px;height:23px;background:var(--blue);color:var(--white);font-size:10px;font-weight:700;
  display:flex;align-items:center;justify-content:center}

/* projects */
.section-bar{position:absolute;left:370px;width:701px;height:41px;background:var(--panel);border:1px solid #eee;
  display:flex;align-items:center;padding-left:34px;font-size:14px;font-weight:700;color:var(--blue);text-transform:uppercase}
.section-bar::before{content:"";position:absolute;left:17px;top:16px;border-left:5px solid var(--orange);border-top:4px solid transparent;border-bottom:4px solid transparent}
.sort{position:absolute;right:12px;top:12px;font-size:8px;font-weight:400;color:#555;display:flex;gap:8px;align-items:center}
.sort b{font-weight:400;width:104px;border-bottom:1px solid #ddd;padding-bottom:2px;position:relative}
.sort b::after{content:"";position:absolute;right:4px;top:2px;width:4px;height:4px;border-right:1px solid #666;border-bottom:1px solid #666;transform:rotate(45deg)}
.project-card{position:absolute;left:370px;width:701px;height:131px;background:#fafafa;border:1px solid #ececec}
.project-thumb{position:absolute;left:0;top:0;width:142px;height:129px}
.project-info{position:absolute;left:167px;top:32px}
.project-info p{font-size:13px;color:#444}
.project-price{font-size:27px;color:var(--blue);line-height:34px}
.project-time{font-size:13px;color:var(--orange);margin-top:4px}

/* testimonials */
.testimonials{position:absolute;left:0;top:1573px;width:1200px;height:397px;background:var(--blue);overflow:hidden}
.testimonial-photo{position:absolute;left:0;top:0;width:480px;height:397px;
  background:linear-gradient(90deg,rgba(40,110,140,.55),rgba(74,174,201,0) 100%)}
.testimonials h2{position:absolute;left:0;width:1200px;top:48px;text-align:center;color:var(--white);font-size:29px;font-weight:400}
.quote-bubble{position:absolute;left:556px;top:127px}
.quote-text{position:absolute;left:0;width:1200px;top:220px;text-align:center;color:var(--white);font-size:21px;line-height:27px}
.quote-author{position:absolute;left:0;width:1200px;top:297px;text-align:center;color:var(--white);font-size:20px;font-weight:700}
.arrow{position:absolute;top:208px}

/* media */
.media{position:absolute;left:0;top:1970px;width:1200px;height:132px;background:#f6f6f6}
.media h3{position:absolute;left:0;width:1200px;top:33px;text-align:center;font-size:11px;letter-spacing:2px;color:var(--orange)}
.media-row{position:absolute;left:230px;top:82px;width:742px;display:flex;justify-content:space-between;align-items:center;color:#333}
.media-row span{font-size:17px;font-weight:700}
.media-row span.sm{font-size:11px;line-height:11px;font-weight:400;text-transform:uppercase}
.media-row span.mid{font-size:13px;font-weight:400;letter-spacing:2px;text-transform:uppercase}

/* footer */
.site-footer{position:absolute;left:0;top:2102px;width:1200px;height:90px;background:#f6f6f6;border-top:1px solid #e3e3e3}
.footer-nav{position:absolute;left:129px;top:22px;font-size:11px;color:#444;text-transform:uppercase;display:flex;gap:9px}
.copyright{position:absolute;left:129px;top:51px;font-size:11px;color:#444}
.connect{position:absolute;left:865px;top:39px;display:flex;align-items:center;gap:5px;font-size:9px;color:#444;text-transform:uppercase}
.connect i{display:block;width:17px;height:17px;border-radius:50%;border:1px solid var(--blue)}
.connect i.red{border-color:#d9534f}
.connect span{margin-right:8px}
</style>
</head>
<body>

<header class="site-header">
  <div class="brand">Pelmora</div>
  <nav class="main-nav">
    <a class="active">Home</a><a>Projects</a><a>How it works</a><a>Plans</a><a>My Account</a>
  </nav>
</header>

<section class="hero">
  <div class="hero-photo" role="img" aria-label="Businessman in a dark suit holding a tablet in an office"></div>
  <div class="hero-panel"></div>
  <h1 class="hero-title">Convert More Customers</h1>
  <p class="hero-sub">Experience the power of experts collaborating on your project.</p>
  <div class="btn-start">Get Started</div>
  <div class="hero-dots"><span class="on"></span><span></span><span></span><span></span></div>
  <div class="hero-aside">
    <h2>True collaboration<br>&amp; teamwork</h2>
    <ul><li>Copywriter</li><li>Graphic designer</li><li>Content marketer</li><li>Creative writer</li></ul>
  </div>
</section>

<aside class="filters">
  <div class="filters-head">Filters</div>
  <div class="filters-body">
    <div class="f-label" style="margin-top:21px">Price</div>
    <div class="price-range"><span>$20</span><span>$1000</span></div>
    <div class="slider"><span></span></div>
    <div class="f-label">Country</div><div class="f-field">Australia</div>
    <div class="f-label">Categories</div><div class="f-field">Graphic Designer</div>
    <div class="f-label">Time Left</div><div class="f-field">2 days</div>
    <div class="f-label">Active | Expired</div><div class="f-field">Active</div>
    <div class="f-label">Contains Adult Content</div><div class="f-field">No</div>
    <div class="f-label">Keywords</div><div class="f-field">Type Your Keywords</div>
    <div class="f-label">Followers</div><div class="f-field">Yes</div>
    <div class="btn-save">Save Filters</div>
  </div>
</aside>

<div class="section-bar" style="top:639px">Crowd Projects
  <div class="sort">SORT: <b>PRICE</b></div>
</div>

<article class="project-card" style="top:702px">
  <div class="project-thumb" role="img" aria-label="Colorful geometric poster artwork" style="background:linear-gradient(135deg,#2d7fa8,#c03a5a 50%,#f0a030)"></div>
  <div class="project-info"><p>Morbi in ante arcu. Maecenas sit amet sem vel</p><div class="project-price">$80, U.K</div><div class="project-time">Time Left: 6 days</div></div>
</article>
<article class="project-card" style="top:852px">
  <div class="project-thumb" role="img" aria-label="Creative triangle badge artwork on light background" style="background:linear-gradient(160deg,#f2f2f4,#c8c6d6 55%,#6a4a8a)"></div>
  <div class="project-info"><p>Lorem ipsum dolor sit amet, consectetur adipiscing</p><div class="project-price">$90, CA.,</div><div class="project-time">Time left: 6 days</div></div>
</article>

<div class="section-bar" style="top:1020px">Featured Projects</div>

<article class="project-card" style="top:1092px">
  <div class="project-thumb" role="img" aria-label="Bright yellow abstract background" style="background:linear-gradient(180deg,#fde14a,#f4b80e)"></div>
  <div class="project-info"><p>Morbi in ante arcu. Maecenas sit amet sem vel</p><div class="project-price">$80, U.K</div><div class="project-time">Time Left: 6 days</div></div>
</article>
<article class="project-card" style="top:1242px">
  <div class="project-thumb" role="img" aria-label="Colorful pop art headline illustration" style="background:radial-gradient(circle at 50% 55%,#c0283c,#f09a2a 45%,#4bb4d6 80%,#fff)"></div>
  <div class="project-info"><p>Lorem ipsum dolor sit amet, consectetur adipiscing</p><div class="project-price">$90, CA.,</div><div class="project-time">Time left: 6 days</div></div>
</article>
<article class="project-card" style="top:1394px">
  <div class="project-thumb" role="img" aria-label="Step-by-step infographic columns" style="background:linear-gradient(90deg,#e8e8e8,#d9dde0 50%,#e6ece8)"></div>
  <div class="project-info" style="left:178px"><p>Lorem ipsum dolor sit amet, consectetur adipiscing</p><div class="project-price">$90, CA.,</div><div class="project-time">Time left: 6 days</div></div>
</article>

<section class="testimonials">
  <div class="testimonial-photo" role="img" aria-label="Man working on a laptop, tinted blue"></div>
  <h2>Testimonials</h2>
  <svg class="quote-bubble" width="80" height="84" viewBox="0 0 80 84" aria-hidden="true">
    <circle cx="40" cy="38" r="38" fill="#f7941d"/>
    <path d="M14 62 L4 80 L30 72 Z" fill="#f7941d"/>
    <text x="40" y="58" text-anchor="middle" fill="#fff" font-family="PT Sans, sans-serif" font-weight="700" font-size="46">&#8220;</text>
  </svg>
  <p class="quote-text">With Pelmora I have multiple experts perfecting my content and I only pay for the<br>feedback I find valuable. It's perfect</p>
  <p class="quote-author">Dana Merrow, CEO, Halden 9</p>
  <svg class="arrow" style="left:104px" width="14" height="20" viewBox="0 0 14 20" aria-hidden="true"><path d="M11 2 L3 10 L11 18" fill="none" stroke="#fff" stroke-width="2.5"/></svg>
  <svg class="arrow" style="left:1082px" width="14" height="20" viewBox="0 0 14 20" aria-hidden="true"><path d="M3 2 L11 10 L3 18" fill="none" stroke="#fff" stroke-width="2.5"/></svg>
</section>

<section class="media">
  <h3>MEDIA LOGOS</h3>
  <div class="media-row">
    <span class="sm">Westvale<br>Business Journal</span>
    <span>Ledgerly</span>
    <span>KVT 4</span>
    <span class="mid">Market Insight</span>
    <span>Byteline</span>
    <span>Harbor City Times</span>
  </div>
</section>

<footer class="site-footer">
  <nav class="footer-nav"><span>Home</span>|<span>Projects</span>|<span>How it works</span>|<span>Plans</span>|<span>My Account</span></nav>
  <p class="copyright">© 2015 COMPANY NAME | ALL RIGHTS RESERVED</p>
  <div class="connect"><span>Connect with us</span><i></i><i></i><i></i><i class="red"></i><i class="red"></i></div>
</footer>

</body>
</html>
```